New Business Card Design for Manufacturing

We are an engineering/manufacturing company that offers Advanced machining/assembly/engineering services, as well as innovative products for the heavy duty engine cooling markets.

We are looking to get a new business card designed that is clean and modern looking, but still fits the wide range of technical/skilled work we do.

- We hope to use this design as the base for other design work in new Presentations, web, and print work.

Industry/Entity Type

Engineering

Contact Information for Business Card

Our preferred color of blue is (RGB) 22/71/159 but can vary slightly from that color. Our content will be our Logo and full company name (Vantrell Forge Works, Inc.), company address, name, job title, phone number with extension, cell number, fax number, website, and email address on the cards.
We'd like the full company name next to the logo, but we are open to other interpretations of that layout.
Preferably, we would like the back side to be clean with just our logo, and the front to contain all of the contact information.

Colors
2f74b4
0355a3
85abd2

Requirements
Must have
• - Logo, company name, needed content - We are open to interpretation beyond that.
• - Standard size business card.
• - Horizontal orientation.
• - Enough space for lengthy names / job titles (for example, a job title could read "Directory of Human Resources" or "V.P. of Governmental Affairs"). We need this to look clean, whether the title be short (CEO) or long (as described above).

```html
<!DOCTYPE html>
<html lang="en">
<head>
<meta charset="utf-8">
<title>Vantrell Forge Works – Business Card</title>
<link href="https://fonts.googleapis.com/css2?family=Open+Sans:wght@400;600;700&display=swap" rel="stylesheet">
<style>
  :root {
    --page: #3b3b3d;
    --card: #1d1d1f;
    --card-gloss: #303033;
    --gloss-text: #3a3a3d;
    --blue: #0355a3;
    --blue-bright: #2f74b4;
    --blue-soft: #85abd2;
    --grey-strip: #a9b0b8;
    --white: #f4f5f7;
    --muted: #8d9096;
  }
  * { margin: 0; padding: 0; box-sizing: border-box; }
  html, body { width: 799px; height: 1200px; overflow: hidden; }
  body {
    background: var(--page);
    font-family: "Open Sans", Arial, sans-serif;
    position: relative;
  }
  .card {
    position: absolute;
    left: 80px;
    width: 640px;
    height: 366px;
    background: var(--card);
    border-radius: 3px;
    box-shadow: 0 18px 40px rgba(0,0,0,.45);
    overflow: hidden;
  }
  .card--back { top: 110px; }
  .card--front { top: 700px; }

  /* Back side: logo only */
  .back-lockup {
    position: absolute;
    left: 0; right: 0; top: 128px;
    text-align: center;
  }
  .back-lockup .brand-name {
    font-size: 46px;
    font-weight: 700;
    color: var(--gloss-text);
    letter-spacing: 1px;
    text-transform: uppercase;
    line-height: 1;
  }
  .back-lockup .brand-tagline {
    margin-top: 14px;
    font-size: 17px;
    font-weight: 700;
    color: var(--gloss-text);
    letter-spacing: 3px;
    text-transform: uppercase;
  }

  /* Front side */
  .front-lockup { position: absolute; left: 36px; top: 34px; }
  .front-lockup .brand-name {
    font-size: 34px;
    font-weight: 700;
    color: var(--blue-bright);
    text-transform: uppercase;
    letter-spacing: 1px;
    line-height: 1;
  }
  .front-lockup .brand-tagline {
    margin-top: 8px;
    font-size: 12px;
    font-weight: 700;
    color: var(--muted);
    letter-spacing: 2.4px;
    text-transform: uppercase;
  }
  .person { position: absolute; left: 36px; top: 150px; }
  .person-name { font-size: 21px; font-weight: 600; color: var(--blue-bright); }
  .person-title { font-size: 12px; color: var(--white); margin-top: 1px; }
  .person-address { font-size: 13px; color: var(--white); margin-top: 16px; line-height: 1.45; }

  .contact { position: absolute; left: 360px; top: 178px; }
  .company-name { font-size: 14px; font-weight: 600; color: var(--blue-bright); margin-bottom: 8px; }
  .contact-line {
    display: flex; align-items: center; gap: 10px;
    font-size: 13px; color: var(--white); line-height: 20px;
  }
  .contact-line svg { width: 12px; height: 12px; fill: var(--blue-bright); flex: none; }

  .card-bands { position: absolute; left: 0; bottom: 0; width: 640px; height: 80px; }
  .website {
    position: absolute; right: 40px; bottom: 20px;
    font-size: 14px; color: var(--white);
  }
</style>
</head>
<body>

  <section class="card card--back" aria-label="Card back">
    <div class="back-lockup">
      <div class="brand-name">Vantrell Forge</div>
      <div class="brand-tagline">Built to Endure</div>
    </div>
  </section>

  <section class="card card--front" aria-label="Card front">
    <div class="front-lockup">
      <div class="brand-name">Vantrell Forge</div>
      <div class="brand-tagline">Built to Endure</div>
    </div>

    <div class="person">
      <div class="person-name">Marlon Reese Tate</div>
      <div class="person-title">Managing Director</div>
      <div class="person-address">58 Kestrel Row, Dunmore,<br>OH 44120</div>
    </div>

    <div class="contact">
      <div class="company-name">Vantrell Forge Works, Inc.</div>
      <div class="contact-line">
        <svg viewBox="0 0 24 24" aria-hidden="true"><path d="M6.6 10.8a15.1 15.1 0 0 0 6.6 6.6l2.2-2.2a1 1 0 0 1 1-.25 11.4 11.4 0 0 0 3.6.57 1 1 0 0 1 1 1V20a1 1 0 0 1-1 1A17 17 0 0 1 3 4a1 1 0 0 1 1-1h3.5a1 1 0 0 1 1 1c0 1.25.2 2.45.57 3.57a1 1 0 0 1-.25 1z"/></svg>
        555-0142-1180 (VFW)
      </div>
      <div class="contact-line">
        <svg viewBox="0 0 24 24" aria-hidden="true"><path d="M7 1h10a2 2 0 0 1 2 2v18a2 2 0 0 1-2 2H7a2 2 0 0 1-2-2V3a2 2 0 0 1 2-2zm0 3v14h10V4zm5 15.5a1.2 1.2 0 1 0 0 2.4 1.2 1.2 0 0 0 0-2.4z"/></svg>
        555-0163-2291
      </div>
      <div class="contact-line">
        <svg viewBox="0 0 24 24" aria-hidden="true"><path d="M6 2h9l3 3v5h2a2 2 0 0 1 2 2v8a2 2 0 0 1-2 2H4a2 2 0 0 1-2-2v-8a2 2 0 0 1 2-2h2zm2 2v6h8V6h-3V4zm9 10a1.2 1.2 0 1 0 0 2.4 1.2 1.2 0 0 0 0-2.4z"/></svg>
        555-0178-3304
      </div>
      <div class="contact-line">
        <svg viewBox="0 0 24 24" aria-hidden="true"><path d="M2 5h20v14H2zm2 2v.5l8 5 8-5V7zm0 2.8V17h16V9.8l-8 5z"/></svg>
        mtate@vantrellforge.com
      </div>
    </div>

    <svg class="card-bands" viewBox="0 0 640 80" aria-hidden="true">
      <rect x="0" y="12" width="310" height="8" fill="var(--grey-strip)"/>
      <path d="M300 12 H640 V80 H330 Q318 22 300 12 Z" fill="var(--blue)"/>
    </svg>
    <div class="website">www.vantrellforge.com</div>
  </section>

</body>
</html>
```